Larkfield Ridge Management

I need a professional website. My current website is larkfieldridgemanagement.com and I hate it. It was created with some AI tool very quickly because I needed a site up and running with no advanced notice. I’m open to all designs .. I trust you, the professionals will deliver the results I’m anxiously awaiting! :)

```html
<!DOCTYPE html>
<html lang="en">
<head>
<meta charset="utf-8">
<title>Larkfield Ridge Management</title>
<link rel="stylesheet" href="https://fonts.googleapis.com/css2?family=Cormorant+Garamond:wght@600;700&family=Jost:wght@400;500;600;700&display=swap">
<style>
:root{
  --navy:#1f2d57;
  --navy-deep:#0b1026;
  --red:#b01c22;
  --red-dark:#8e1319;
  --white:#ffffff;
  --ink:#111111;
  --grey-band:#6f6f6f;
  --light:#f4f6fa;
  --card:#f6f6f6;
  --field:#c9ccd4;
  --serif:'Cormorant Garamond',Georgia,serif;
  --sans:'Jost',Arial,sans-serif;
}
*{box-sizing:border-box;margin:0;padding:0}
html,body{width:1200px;height:3019px;overflow:hidden}
body{position:relative;background:var(--white);font-family:var(--sans);color:var(--ink)}
.abs{position:absolute}

/* hero */
.hero{left:0;top:0;width:1200px;height:688px;
  background:linear-gradient(180deg,#18213d 0%,#3a3f6a 22%,#8a6a8c 38%,#d99a74 50%,#6f7aa0 62%,#2c3444 78%,#2f4424 90%,#24361c 100%)}
.brand{color:var(--white);font-family:var(--sans);font-weight:700;font-size:17px;line-height:1.1;display:flex;align-items:center;gap:10px}
.brand .dot{width:16px;height:16px;border-radius:50%;background:var(--red)}
.nav{display:flex;gap:33px;font-size:11.5px;font-weight:600;letter-spacing:.3px;color:var(--white)}
.btn{background:var(--red);color:var(--white);font-family:var(--sans);font-weight:600;font-size:13px;display:flex;align-items:center;justify-content:center;letter-spacing:.2px}
.btn.cta-nav{left:900px;top:16px;width:206px;height:48px;border-bottom:3px solid var(--red-dark)}
.hero-title{left:0;width:1200px;top:102px;color:var(--white);font-family:var(--serif);font-weight:700;font-size:53px;line-height:60px;letter-spacing:1px;text-align:center}
.hero-title .line{display:flex;justify-content:center;align-items:center;gap:12px}
.hero-title .rule{width:76px;height:3px;background:var(--red);flex:none}
.hero-sub{left:0;width:1200px;top:230px;text-align:center;color:var(--white);font-size:11px}
.btn.cta-hero{left:499px;top:260px;width:205px;height:47px;border-bottom:3px solid var(--red-dark)}

/* stats */
.stats{left:0;top:688px;width:1200px;height:112px;background:var(--grey-band)}
.stat{display:flex;align-items:center;gap:12px;color:var(--white)}
.stat b{display:block;font-size:31px;font-weight:600;line-height:30px}
.stat span{font-size:11.5px}
.divider{top:716px;width:1px;height:58px;background:rgba(255,255,255,.5)}
.stripes{left:0;top:800px;width:1200px;height:12px;background:linear-gradient(180deg,var(--red) 0 4px,var(--white) 4px 7px,var(--navy) 7px 12px)}

/* services */
.eyebrow{left:0;width:1200px;top:902px;display:flex;justify-content:center;align-items:center;gap:14px;font-size:23px;font-weight:500}
.eyebrow i{width:52px;height:2px;background:var(--red);display:block}
.section-title{font-family:var(--serif);font-weight:700;font-size:39px;line-height:47px;letter-spacing:1.5px;text-align:center}
.card{top:1056px;width:497px;height:363px;background:var(--card);box-shadow:0 2px 8px rgba(0,0,0,.12)}
.card .photo{height:265px}
.card h3{font-family:var(--serif);font-weight:600;font-size:25px;letter-spacing:1px;margin:18px 0 0 23px}
.card p{font-size:11px;margin:6px 0 0 23px}

/* onboarding */
.dash{left:0;top:1600px;width:1200px;border-top:1.5px dashed #c4c4c4}
.step{width:200px;text-align:center}
.step .label{font-size:23px;font-weight:500;margin-top:8px;letter-spacing:.3px}

/* why */
.why-photo{left:0;top:1793px;width:600px;height:407px;
  background:linear-gradient(90deg,#7d6a55 0%,#b9a58c 40%,#e3dcd2 70%,#ffffff 100%)}
.why-title{left:698px;top:1828px;font-family:var(--serif);font-weight:700;font-size:38px;line-height:47px;letter-spacing:1.5px}
.reason{left:697px;display:flex;gap:17px}
.reason h4{font-size:24px;font-weight:500;line-height:26px}
.reason p{font-size:10.5px;margin-top:7px}

/* proposal */
.proposal{left:0;top:2200px;width:1200px;height:401px;background:var(--light)}
.proposal-title{left:94px;top:2260px;font-family:var(--serif);font-weight:700;font-size:39px;line-height:47px;letter-spacing:1px}
.proposal-text{left:91px;top:2405px;width:340px;font-size:11px;line-height:16px}
.field{border:1px solid var(--field);background:var(--light);font-size:11px;color:#8c8f98;padding:12px 13px}
.btn.submit{left:581px;top:2503px;width:525px;height:43px}

/* footer */
.footer{left:0;top:2601px;width:1200px;height:418px;background:var(--navy-deep)}
.footer-brand{left:0;width:1200px;top:2725px;display:flex;justify-content:center;align-items:center;gap:12px;color:var(--white);font-weight:700;font-size:30px}
.footer-brand .dot{width:26px;height:26px;border-radius:50%;background:var(--red)}
.social{top:2907px;width:30px;height:30px;border-radius:50%;background:var(--white)}
.footer-line{left:0;top:2973px;width:1200px;height:1px;background:rgba(255,255,255,.35)}
.copy{left:0;width:1200px;top:2990px;text-align:center;color:var(--white);font-size:11.5px}
</style>
</head>
<body>

<header>
  <div class="abs hero" role="img" aria-label="Modern multi-level glass house at sunset surrounded by pine trees"></div>
  <div class="abs brand" style="left:94px;top:52px"><span class="dot"></span>Larkfield Ridge<br>Management</div>
  <nav class="abs nav" style="left:349px;top:32px">
    <span>RESIDENTIAL</span><span>COMMERCIAL</span><span>ABOUT</span><span>SERVICE</span><span>AREA</span><span>RESOURCES</span>
  </nav>
  <a class="abs btn cta-nav">REQUEST A PROPOSAL</a>
  <h1 class="abs hero-title">
    <div class="line">A TRUE PARTNER,</div>
    <div class="line"><span class="rule"></span><span>NOT JUST A VENDOR</span><span class="rule"></span></div>
  </h1>
  <p class="abs hero-sub">Residential And Commercial Management Across Cleveland And Akron. Direct Communication, Transparent Fees.</p>
  <a class="abs btn cta-hero">GET A FREE ASSESSMENT</a>
</header>

<section>
  <div class="abs stats"></div>
  <div class="abs stat" style="left:123px;top:716px">
    <svg width="44" height="44" viewBox="0 0 44 44" fill="none" stroke="#fff" stroke-width="2.4"><path d="M4 22 22 6l18 16M9 18v20h10V27h6v11h10V18"/></svg>
    <div><b>500+</b><span>Properties Managed</span></div>
  </div>
  <div class="abs divider" style="left:347px"></div>
  <div class="abs stat" style="left:412px;top:716px">
    <svg width="44" height="44" viewBox="0 0 44 44" fill="none" stroke="#fff" stroke-width="2"><circle cx="22" cy="22" r="9"/><circle cx="22" cy="22" r="4"/><path d="M15 30l-4 9 5-2 3 4 3-8M29 30l4 9-5-2-3 4-3-8M22 4l1.5 3 3 .4-2.2 2 .6 3-2.9-1.5-2.9 1.5.6-3-2.2-2 3-.4z"/></svg>
    <div><b>15</b><span>Years Experience</span></div>
  </div>
  <div class="abs divider" style="left:618px"></div>
  <div class="abs stat" style="left:682px;top:716px">
    <svg width="44" height="44" viewBox="0 0 44 44" fill="none" stroke="#fff" stroke-width="2"><rect x="4" y="22" width="36" height="16"/><circle cx="14" cy="12" r="5"/><circle cx="30" cy="12" r="5"/><path d="M4 30h36M16 22v16M28 22v16"/></svg>
    <div><b>98%</b><span>Occupancy Rate</span></div>
  </div>
  <div class="abs divider" style="left:883px"></div>
  <div class="abs stat" style="left:947px;top:716px">
    <svg width="44" height="44" viewBox="0 0 44 44" fill="none" stroke="#fff" stroke-width="2"><path d="M8 24v-4a14 14 0 0 1 28 0v4"/><rect x="5" y="22" width="6" height="10" rx="2"/><rect x="33" y="22" width="6" height="10" rx="2"/><path d="M16 18h14a3 3 0 0 1 3 3v6a3 3 0 0 1-3 3h-7l-5 4v-4h-2a3 3 0 0 1-3-3v-6a3 3 0 0 1 3-3z"/></svg>
    <div><b>24/7</b><span>Owner Support</span></div>
  </div>
  <div class="abs stripes"></div>
</section>

<section>
  <div class="abs eyebrow"><i></i>SERVICES<i></i></div>
  <h2 class="abs section-title" style="left:0;width:1200px;top:944px">STRATEGIC PROPERTY<br>MANAGEMENT SOLUTIONS</h2>
  <article class="abs card" style="left:94px">
    <div class="photo" role="img" aria-label="White two-storey residential house with dark roofs beside a driveway and bare trees" style="background:linear-gradient(180deg,#9aa3ad 0%,#d4d6d8 45%,#6c7268 80%,#5a6350 100%)"></div>
    <h3>RESIDENTIAL</h3>
    <p>Tenant Screening, Rent Collection, Maintenance Coordination, Owner Reporting.</p>
  </article>
  <article class="abs card" style="left:609px">
    <div class="photo" role="img" aria-label="Glass commercial office towers above green trees under a blue sky" style="background:linear-gradient(180deg,#3f86d0 0%,#8fbde4 40%,#4f7fa8 70%,#3d7a2c 100%)"></div>
    <h3>COMMERCIAL</h3>
    <p>Lease Administration, Vendor Management, CAM Reconciliation, Reporting.</p>
  </article>
</section>

<section>
  <h2 class="abs section-title" style="left:0;width:1200px;top:1484px;font-size:37px">WHAT ONBOARDING LOOKS LIKE</h2>
  <div class="abs dash"></div>

  <div class="abs step" style="left:110px;top:1564px">
    <svg width="104" height="100" viewBox="0 0 104 100"><path d="M3 0h98v58L52 76 3 58z" fill="#fff"/><path d="M7 3h90v52L52 71 7 55z" fill="var(--navy)"/><g fill="none" stroke="#fff" stroke-width="1.6"><rect x="41" y="20" width="22" height="28"/><path d="M45 27h3M51 27h8M45 34h3M51 34h8M45 41h3M51 41h8"/></g><circle cx="50" cy="82" r="15" fill="var(--red)"/><text x="50" y="88" text-anchor="middle" fill="#fff" font-family="Jost,sans-serif" font-size="17" font-weight="500">1</text></svg>
    <div class="label">ASSESSMENT</div>
  </div>
  <div class="abs step" style="left:385px;top:1564px">
    <svg width="104" height="100" viewBox="0 0 104 100"><path d="M3 0h98v58L52 76 3 58z" fill="#fff"/><path d="M7 3h90v52L52 71 7 55z" fill="var(--navy)"/><g fill="none" stroke="#fff" stroke-width="1.6"><circle cx="43" cy="24" r="4"/><circle cx="61" cy="24" r="4"/><path d="M49 24h6M40 36h8v8h-8zM56 36h8v8h-8zM52 28v6"/></g><circle cx="50" cy="82" r="15" fill="var(--red)"/><text x="50" y="88" text-anchor="middle" fill="#fff" font-family="Jost,sans-serif" font-size="17" font-weight="500">2</text></svg>
    <div class="label">ONBOARDING</div>
  </div>
  <div class="abs step" style="left:648px;top:1564px">
    <svg width="104" height="100" viewBox="0 0 104 100"><path d="M3 0h98v58L52 76 3 58z" fill="#fff"/><path d="M7 3h90v52L52 71 7 55z" fill="var(--navy)"/><g fill="none" stroke="#fff" stroke-width="1.6"><path d="M38 34 52 20l14 14v14H38z"/><circle cx="52" cy="37" r="5"/></g><circle cx="50" cy="82" r="15" fill="var(--red)"/><text x="50" y="88" text-anchor="middle" fill="#fff" font-family="Jost,sans-serif" font-size="17" font-weight="500">3</text></svg>
    <div class="label">MANAGEMENT</div>
  </div>
  <div class="abs step" style="left:896px;top:1564px">
    <svg width="104" height="100" viewBox="0 0 104 100"><path d="M3 0h98v58L52 76 3 58z" fill="#fff"/><path d="M7 3h90v52L52 71 7 55z" fill="var(--navy)"/><g fill="none" stroke="#fff" stroke-width="1.6"><path d="M40 20h18v28H40zM44 28h10M44 34h8M44 40h6M52 46l12-14 3 3-12 14-4 1z"/></g><circle cx="50" cy="82" r="15" fill="var(--red)"/><text x="50" y="88" text-anchor="middle" fill="#fff" font-family="Jost,sans-serif" font-size="17" font-weight="500">4</text></svg>
    <div class="label">REPORTING</div>
  </div>
</section>

<section>
  <div class="abs why-photo" role="img" aria-label="Bright living room with chandelier, sofa, coffee table and wooden cabinets"></div>
  <h2 class="abs why-title">WHY OWNERS<br>CHOOSE US</h2>
  <div class="abs reason" style="top:1938px">
    <svg width="44" height="44" viewBox="0 0 44 44" fill="none" stroke="var(--red)" stroke-width="2"><path d="M16 14h22a3 3 0 0 1 3 3v9a3 3 0 0 1-3 3h-6l-4 4v-4H16a3 3 0 0 1-3-3v-9a3 3 0 0 1 3-3z"/><path d="M13 20H6a3 3 0 0 0-3 3v9a3 3 0 0 0 3 3h3v4l4-4h6a3 3 0 0 0 3-3"/></svg>
    <div><h4>TALK TO A PERSON</h4><p>No Call Center, No Ticket Queue.</p></div>
  </div>
  <div class="abs reason" style="top:2014px">
    <svg width="44" height="44" viewBox="0 0 44 44" fill="none" stroke="var(--red)" stroke-width="2"><path d="M6 10l14-6 10 22-14 6zM10 34l10 6 10-4M13 16l3 7"/></svg>
    <div><h4>TRANSPARENT FEES</h4><p>No Hidden Markups, Ever.</p></div>
  </div>
  <div class="abs reason" style="top:2090px">
    <svg width="44" height="44" viewBox="0 0 44 44" fill="none" stroke="var(--red)" stroke-width="2"><path d="M4 14h16v24H4zM24 14h16v24H24zM20 38h4M8 20h8M8 26h8M28 20h8M28 26h8M22 4v5M16 6l2 3M28 6l-2 3"/></svg>
    <div><h4>LOCAL KNOWLEDGE</h4><p>Cleveland-Akron Only, Block By Block.</p></div>
  </div>
</section>

<section>
  <div class="abs proposal"></div>
  <h2 class="abs proposal-title">REQUEST A CUSTOM<br>MANAGEMENT<br>PROPOSAL</h2>
  <p class="abs proposal-text">Submit The Inquiry Form To Connect With A Dedicated Advisor Who Will Evaluate Your Objectives And Implement A Strategic Management Plan Tailored To Your Portfolio.</p>
  <div class="abs field" style="left:581px;top:2270px;width:258px;height:43px">First Name</div>
  <div class="abs field" style="left:848px;top:2270px;width:258px;height:43px">Second Name</div>
  <div class="abs field" style="left:581px;top:2324px;width:258px;height:43px">E-Mail</div>
  <div class="abs field" style="left:848px;top:2324px;width:258px;height:43px">Phone</div>
  <div class="abs field" style="left:581px;top:2377px;width:525px;height:112px">Message</div>
  <a class="abs btn submit">SUBMIT</a>
</section>

<footer>
  <div class="abs footer"></div>
  <div class="abs footer-brand"><span class="dot"></span>Larkfield Ridge Management</div>
  <nav class="abs nav" style="left:349px;top:2870px">
    <span>RESIDENTIAL</span><span>COMMERCIAL</span><span>ABOUT</span><span>SERVICE</span><span>AREA</span><span>RESOURCES</span>
  </nav>
  <div class="abs social" style="left:565px"></div>
  <div class="abs social" style="left:605px"></div>
  <div class="abs footer-line"></div>
  <p class="abs copy">© Larkfield Ridge Management LLC .All Rights Reserved.2026</p>
</footer>

</body>
</html>
```